Alloy wheel repair business needs a website

Install logo previously purchased from makerhive, toolbar with dropdowns. services, gallery, clients , contact ect
Maybe mission statment

Target Market(s)

vehicle owners, auto dealers,insurance companies,

Industry/Entity Type

Alloy Wheel Repair

Coding

Coded - Design and coding required

Number of Pages Required

4 page

Font styles to use
Sans Serif

Colors
0054AA
0677BA
7BADD7
CADEEF
E8F1F8

```html
<!DOCTYPE html>
<html lang="en">
<head>
<meta charset="utf-8">
<title>Rimline Wheelcraft</title>
<link href="https://fonts.googleapis.com/css2?family=Audiowide&family=Roboto:ital,wght@0,400;0,500;0,700;1,400;1,500&display=swap" rel="stylesheet">
<style>
:root{
  --blue-deep:#0054AA;
  --blue:#3d8fd6;
  --blue-mid:#0677BA;
  --sky:#45c6f2;
  --ink:#1b1b1b;
  --text:#555;
  --dark:#1f1f1f;
  --white:#fff;
  --pale:#E8F1F8;
}
*{margin:0;padding:0;box-sizing:border-box}
html,body{width:1200px;height:4677px;overflow:hidden;background:var(--white)}
body{position:relative;font-family:"Roboto",Arial,sans-serif;color:var(--text)}
.abs{position:absolute}
.display{font-family:"Audiowide","Roboto",sans-serif;text-transform:uppercase;letter-spacing:1px}
.btn{position:absolute;display:flex;align-items:center;justify-content:center;background:var(--blue);color:var(--white);font-family:"Audiowide",sans-serif;text-transform:uppercase;font-size:17px;letter-spacing:1px}
.btn-outline{position:absolute;display:flex;align-items:center;justify-content:center;border:2px solid var(--blue);color:var(--blue);font-size:15px;font-weight:500}
.photo{position:absolute}

/* header */
.topbar{left:604px;top:0;width:596px;height:51px;background:linear-gradient(90deg,var(--blue),var(--sky));clip-path:polygon(4% 0,100% 0,100% 100%,0 100%);display:flex;align-items:center;gap:34px;padding-left:40px;color:var(--white);font-size:17px}
.topbar span{display:flex;align-items:center;gap:8px}
.brand{left:127px;top:30px;font-family:"Roboto",sans-serif;font-weight:700;font-size:33px;color:var(--blue-deep);letter-spacing:1px;display:flex;align-items:center;gap:10px}
.brand i{display:block;width:22px;height:22px;border-radius:50%;background:var(--blue-deep)}
.nav{top:80px;font-family:"Audiowide",sans-serif;font-size:17px;color:var(--ink);letter-spacing:1px}
.nav.active{color:var(--blue)}

/* hero */
.hero-photo{left:0;top:131px;width:1200px;height:622px;background:linear-gradient(90deg,#2e4f7a 0%,#4b5360 35%,#3a3a3c 55%,#0c0c0c 75%,#000 100%)}
.hero-title{left:690px;top:232px;color:var(--white);font-size:52px;line-height:60px;letter-spacing:3px}
.hero-text{left:690px;top:357px;width:390px;color:var(--white);font-size:20px;line-height:24px}

/* about */
.section-title{width:1200px;left:0;text-align:center;color:var(--ink);font-size:36px;letter-spacing:2px}
.sub-title{color:var(--blue);font-size:23px;letter-spacing:1.5px}
.para{font-size:14.5px;line-height:18px;color:#444}

/* services */
.services-band{left:0;top:1434px;width:1200px;height:700px;background:linear-gradient(90deg,#3a88d2,#45c8f3)}
.card{position:absolute;top:1597px;width:296px;height:403px;background:var(--white)}
.card .photo{left:13px;top:15px;width:270px;height:185px}
.card h3{position:absolute;top:242px;width:100%;text-align:center;font-family:"Audiowide",sans-serif;font-size:21px;color:var(--ink);letter-spacing:1px;font-weight:400}
.card p{position:absolute;top:273px;left:40px;right:40px;text-align:center;font-size:14.5px;line-height:18px;color:#666}
.card .btn-outline{top:338px;left:91px;width:114px;height:38px}
.arrow{position:absolute;top:1695px}

/* schedule */
.schedule-band{left:272px;top:2773px;width:799px;height:269px;background:linear-gradient(90deg,#3a88d2,#45c8f3)}

/* footer */
.foot-head{font-family:"Audiowide",sans-serif;color:var(--sky);font-size:20px;letter-spacing:1px}
.foot-list{color:#ddd;font-size:14.5px;line-height:26.5px}
</style>
</head>
<body>

<!-- Header -->
<div class="abs topbar">
  <span><svg width="16" height="12" viewBox="0 0 16 12"><rect width="16" height="12" rx="1" fill="#fff"/><path d="M0 1 L8 7 L16 1" stroke="#3d8fd6" stroke-width="1.6" fill="none"/></svg>sam@rimlinewheelcraft.com</span>
  <span><svg width="15" height="15" viewBox="0 0 24 24"><path fill="#fff" d="M6.6 10.8c1.4 2.8 3.8 5.1 6.6 6.6l2.2-2.2c.3-.3.7-.4 1-.2 1.1.4 2.3.6 3.6.6.6 0 1 .4 1 1V20c0 .6-.4 1-1 1C10.6 21 3 13.4 3 4c0-.6.4-1 1-1h3.5c.6 0 1 .4 1 1 0 1.3.2 2.5.6 3.6.1.3 0 .7-.2 1z"/></svg>Call: 555-014-2780</span>
</div>
<div class="abs brand"><i></i>Rimline Wheelcraft</div>
<div class="abs nav active" style="left:421px">Home</div>
<div class="abs nav" style="left:530px">Services<span style="font-size:10px">▾</span></div>
<div class="abs nav" style="left:684px">Gallery</div>
<div class="abs nav" style="left:831px">Clients</div>
<div class="abs nav" style="left:964px">Contact</div>

<!-- Hero -->
<div class="photo hero-photo" role="img" aria-label="Mechanic fitting a tyre onto a car wheel with an impact wrench in a workshop"></div>
<svg class="abs" style="left:0;top:131px" width="1200" height="640" viewBox="0 0 1200 640">
  <path d="M0 520 C300 700 800 600 1200 250 L1200 300 C820 640 320 720 0 610 Z" fill="#000"/>
  <path d="M0 610 C320 720 820 640 1200 300 L1200 640 L0 640 Z" fill="#fff"/>
  <circle cx="1094" cy="406" r="35" fill="#fff" stroke="#e0e6ee" stroke-width="3"/>
  <circle cx="1094" cy="406" r="20" fill="#0054AA"/>
</svg>
<div class="abs display hero-title">Rimline<br>Wheelcraft</div>
<div class="abs hero-text">Lorem ipsum dolor sit amet, consectetur adipiscing elit, sed do eiusmod.</div>
<div class="btn" style="left:686px;top:425px;width:203px;height:58px">Get a Quote</div>

<!-- About -->
<div class="abs display section-title" style="top:824px">About Us</div>
<div class="abs display sub-title" style="left:127px;top:930px">Our Mission</div>
<p class="abs para" style="left:127px;top:975px;width:450px">Lorem ipsum dolor sit amet, consectetur adipiscing elit, sed do eiusmod tempor incididunt ut labore et dolore magna aliqua. Quis ipsum suspendisse ultrices gravida. Risus commodo viverra maec enas accumsan lacus vel facilisis. Lorem ipsum dolor sit amet, consectetur adipiscing elit, sed do eiusmod tempor.</p>
<div class="abs display sub-title" style="left:127px;top:1090px">Our Vision</div>
<p class="abs para" style="left:127px;top:1135px;width:450px">Lorem ipsum dolor sit amet, consectetur adipiscing elit, sed do eiusmod tempor incididunt ut labore et dolore magna aliqua. Quis ipsum suspendisse ultrices gravida. Risus commodo viverra maec enas accumsan lacus vel facilisis. Lorem ipsum dolor sit amet, consectetur adipiscing elit, sed do eiusmod tempor.</p>
<div class="btn" style="left:127px;top:1249px;width:176px;height:51px;font-size:16px">Read More</div>

<svg class="abs" style="left:620px;top:870px" width="480" height="460" viewBox="0 0 480 460">
  <path d="M248 12 A206 206 0 1 1 60 340 A196 196 0 1 0 248 12 Z" fill="#000"/>
  <path d="M60 340 A206 206 0 0 0 460 280 A200 200 0 0 1 60 340 Z" fill="#000"/>
</svg>
<div class="photo" role="img" aria-label="Hands in red gloves balancing an alloy wheel on a car" style="left:643px;top:900px;width:396px;height:396px;border-radius:50%;background:radial-gradient(circle at 40% 30%,#e98a6a,#5a6e9c 45%,#1e2c5a 80%)"></div>
<div class="abs" style="left:648px;top:1183px;width:66px;height:66px;border-radius:50%;background:#fff;box-shadow:0 2px 6px rgba(0,0,0,.2)"></div>
<div class="abs" style="left:664px;top:1199px;width:34px;height:34px;border-radius:50%;background:var(--blue-deep)"></div>

<!-- Services -->
<div class="abs services-band"></div>
<div class="abs display section-title" style="top:1510px;color:#fff">Our Services</div>
<svg class="arrow" style="left:76px" width="22" height="22" viewBox="0 0 22 22"><circle cx="11" cy="11" r="9.5" fill="none" stroke="#fff" stroke-width="2"/><path d="M13 6 L8 11 L13 16" fill="none" stroke="#fff" stroke-width="2"/></svg>
<svg class="arrow" style="left:1100px" width="22" height="22" viewBox="0 0 22 22"><circle cx="11" cy="11" r="9.5" fill="none" stroke="#fff" stroke-width="2"/><path d="M9 6 L14 11 L9 16" fill="none" stroke="#fff" stroke-width="2"/></svg>

<div class="card" style="left:127px">
  <div class="photo" role="img" aria-label="Technician repairing a wheel in a workshop" style="background:linear-gradient(135deg,#1f3f7a,#c58a4a 55%,#2a2a2a)"></div>
  <h3>Repairs</h3>
  <p>Lorem ipsum dolor sit amet, consectetur adipiscing elit, sed do eiusmod tempor incina.</p>
  <div class="btn-outline">Read More</div>
</div>
<div class="card" style="left:450px">
  <div class="photo" role="img" aria-label="Alloy rim being refinished on a workbench" style="background:linear-gradient(135deg,#3b3b3b,#b9b9b9 55%,#6b6b6b)"></div>
  <h3>Refinish</h3>
  <p>Lorem ipsum dolor sit amet, consectetur adipiscing elit, sed do eiusmod tempor incina.</p>
  <div class="btn-outline">Read More</div>
</div>
<div class="card" style="left:775px">
  <div class="photo" role="img" aria-label="Tyre and wheel fitted on a vehicle" style="background:linear-gradient(135deg,#d8dce2,#6c7582 45%,#1d1f23)"></div>
  <h3>Flare Kits</h3>
  <p>Lorem ipsum dolor sit amet, consectetur adipiscing elit, sed do eiusmod tempor incina.</p>
  <div class="btn-outline">Read More</div>
</div>

<!-- Why choose us -->
<div class="photo" role="img" aria-label="Gloved hands holding a tyre" style="left:18px;top:2311px;width:278px;height:315px;background:linear-gradient(160deg,#3a66b8,#2b2b2b 55%,#111)"></div>
<div class="photo" role="img" aria-label="Mechanic working on a car wheel in a garage" style="left:310px;top:2271px;width:313px;height:328px;background:linear-gradient(135deg,#7a8796,#c9ced4 40%,#4a4f55)"></div>
<div class="abs display" style="left:661px;top:2298px;font-size:36px;line-height:42px;color:var(--ink)">Why<br>Choose Us?</div>
<p class="abs para" style="left:661px;top:2397px;width:420px;color:#555">Sed ut perspiciatis unde omnis iste natus error sit voluptatem accusantium doloremque laudantium, totam rem aperiam, eaque ipsa quae ab illo inventore veritatis et quasi architecto beatae vitae dicta sunt explicabo. Nemo enim ipsam volupta tem quia voluptas sit aspernatur aut odit aut fugit, sed quia consequuntur magni dolores eos qui ratione voluptatem sequi nesciunt. Neque porro quisquam est, qui dolorem ipsum quia dolor sit amet, consectetur, adipisci velit, sed quia non um quam eius modi tempora incidunt ut labore et dolore magn am aliquam quaerat voluptatem.</p>
<div class="btn" style="left:661px;top:2603px;width:203px;height:58px">Get a Quote</div>

<!-- Schedule -->
<div class="abs schedule-band"></div>
<div class="photo" role="img" aria-label="Stack of tyres with alloy wheels" style="left:33px;top:2745px;width:330px;height:310px;border-radius:40% 20% 20% 40%;background:radial-gradient(circle at 30% 60%,#cfd2d6,#2b2b2b 40%,#111 75%,rgba(17,17,17,0) 100%)"></div>
<div class="photo" role="img" aria-label="Smiling mechanic with crossed arms holding a wrench" style="left:808px;top:2726px;width:236px;height:316px;background:linear-gradient(180deg,rgba(40,50,70,0) 0%,#2c3646 30%,#1e2634 100%);border-radius:45% 45% 0 0"></div>
<div class="abs display" style="left:400px;top:2848px;width:355px;text-align:center;color:#fff;font-size:22px">Schedual a Service</div>
<p class="abs" style="left:370px;top:2896px;width:420px;text-align:center;color:#fff;font-size:14.5px;line-height:18px">Lorem ipsum dolor sit amet, consectetur adipiscing elit, sed do eiusmod tempor incididunt ut labore et dolore .</p>
<div class="abs" style="left:468px;top:2944px;width:218px;height:46px;background:#1a6cc0;border-radius:6px;display:flex;align-items:center;justify-content:center;color:#fff;font-size:22px;font-style:italic;font-weight:500">Call: 555-014-2780</div>

<!-- Gallery -->
<div class="abs display section-title" style="top:3164px">Our Gallery</div>
<div class="photo" role="img" aria-label="Tyre being mounted on a tyre changer" style="left:127px;top:3243px;width:301px;height:396px;background:linear-gradient(160deg,#3a3f4a,#7c6a5a 50%,#1a1a1a)"></div>
<div class="photo" role="img" aria-label="Mechanic fitting an alloy wheel" style="left:447px;top:3243px;width:301px;height:396px;background:linear-gradient(135deg,#9a9a9a,#3a3a3a 50%,#151515)"></div>
<div class="photo" role="img" aria-label="Close view of an alloy wheel on a blue car" style="left:770px;top:3243px;width:301px;height:191px;background:linear-gradient(135deg,#1a2a4a,#3a6ab5 45%,#0c0c10)"></div>
<div class="photo" role="img" aria-label="Wheel being fitted in a workshop at dusk" style="left:770px;top:3447px;width:301px;height:192px;background:linear-gradient(135deg,#c27a3a,#4a3a30 45%,#141414)"></div>
<div class="btn" style="left:519px;top:3668px;width:162px;height:51px;font-size:16px">View More</div>

<!-- Testimonials -->
<div class="abs display section-title" style="top:3859px">Client Testimonials</div>
<div class="photo" role="img" aria-label="Portrait of a client" style="left:187px;top:3962px;width:152px;height:152px;border-radius:50%;background:linear-gradient(180deg,#6a5a4e,#2e2a28 55%,#e0a020)"></div>
<p class="abs" style="left:363px;top:3970px;width:630px;font-size:22px;line-height:26px;font-style:italic;color:#333">Lorem ipsum dolor sit amet, consectetur adipiscing elit, sed do eiusmod tempor incididunt ut labore et dolore magna aliqua. Quis ipsum suspendisse ultrices gravida. Risus commodo viverra maecenas accumsan lacus vel facilisis.</p>
<div class="abs" style="left:363px;top:4087px;font-size:24px;font-weight:500;color:var(--sky)">DANA MILES</div>

<!-- Footer -->
<svg class="abs" style="left:0;top:4160px" width="1200" height="517" viewBox="0 0 1200 517">
  <path d="M0 30 C300 0 420 80 600 80 C800 80 950 0 1200 20 L1200 517 L0 517 Z" fill="#1f1f1f"/>
</svg>
<div class="abs" style="left:127px;top:4385px;font-weight:700;font-size:30px;color:#fff;letter-spacing:1px;line-height:36px">Rimline<br>Wheelcraft</div>
<div class="abs" style="left:162px;top:4450px;display:flex;gap:20px">
  <span style="width:20px;height:20px;border-radius:50%;background:var(--sky)"></span>
  <span style="width:20px;height:20px;border-radius:50%;background:var(--sky)"></span>
  <span style="width:20px;height:20px;border-radius:50%;background:var(--sky)"></span>
</div>

<div class="abs foot-head" style="left:397px;top:4330px;font-size:17px">Home</div>
<div class="abs foot-list" style="left:397px;top:4361px">About<br>Services<br>Pricing<br>Gallery<br>Contact</div>

<div class="abs foot-head" style="left:545px;top:4328px">Hours</div>
<div class="abs foot-list" style="left:545px;top:4361px">Mon<br>Tue<br>Wed<br>Thu<br>Friday<br>Saturday<br>Sunday</div>
<div class="abs foot-list" style="left:630px;top:4361px">7:00am - 5:00pm<br>7:00am - 5:00pm<br>7:00am - 5:00pm<br>7:00am - 5:00pm<br>7:00am - 5:00pm<br>7:00am - 12:00pm<br>Closed</div>

<div class="abs foot-head" style="left:826px;top:4328px">Contact Us</div>
<svg class="abs" style="left:826px;top:4375px" width="22" height="22" viewBox="0 0 24 24"><path fill="#45c6f2" d="M6.6 10.8c1.4 2.8 3.8 5.1 6.6 6.6l2.2-2.2c.3-.3.7-.4 1-.2 1.1.4 2.3.6 3.6.6.6 0 1 .4 1 1V20c0 .6-.4 1-1 1C10.6 21 3 13.4 3 4c0-.6.4-1 1-1h3.5c.6 0 1 .4 1 1 0 1.3.2 2.5.6 3.6.1.3 0 .7-.2 1z"/></svg>
<div class="abs" style="left:867px;top:4368px;color:#ddd;font-size:14.5px;line-height:19px">Call Us:<br>555-014-2780</div>
<svg class="abs" style="left:828px;top:4447px" width="20" height="15" viewBox="0 0 16 12"><rect width="16" height="12" rx="1" fill="#45c6f2"/><path d="M0 1 L8 7 L16 1" stroke="#1f1f1f" stroke-width="1.4" fill="none"/></svg>
<div class="abs" style="left:867px;top:4432px;color:#ddd;font-size:14.5px;line-height:19px">Email:<br>sam@rimlinewheelcraft.com</div>
<svg class="abs" style="left:828px;top:4500px" width="18" height="26" viewBox="0 0 18 26"><path fill="#45c6f2" d="M9 0C4 0 0 4 0 9c0 7 9 17 9 17s9-10 9-17c0-5-4-9-9-9zm0 12.5A3.5 3.5 0 1 1 9 5.5a3.5 3.5 0 0 1 0 7z"/></svg>
<div class="abs" style="left:867px;top:4498px;color:#ddd;font-size:14.5px;line-height:19px">Address: 742 Orchard Lane<br>Millbrook PA 10000</div>

<div class="abs" style="left:112px;top:4596px;width:973px;height:1px;background:#555"></div>
<div class="abs" style="left:0;top:4620px;width:1200px;text-align:center;color:#ddd;font-size:14px">Copyright 2023 All rights are reserved.</div>

</body>
</html>
```